Brevard Trade Partners - we are Asian sourcing agents

We are sourcing agents based in the USA and we act as sourcing agents for clients in throughout the world. We focus primarily on custom sewn goods. So basically companies who do not have the in-house expertise to do it themselves, come to us and have us find suitable factories in Asia to do the production. We are middlemen. We find the factories...quote the project...manage the quality control and then deliver the goods directly to our customer's door. We pride ourselves in making the communication very easy and precise.

Current page is www.brevardtradepartners.com

I am not happy w/ the overall look. The spacing...the photos, the fonts...the design elements...the pictures. I want a cool, crisp design that conveys professionalism and clearly depicts/explains what we do.

Requirements
Must have
• use my logo....I like it...it was designed by someone on this website.
Nice to have
• a video/animation of the entire process would be wonderful. Showing initial contact with our office in the USA...then to my correspondence with my offices in Taiwan and in Hong Kong...and then back and fort w/ the customer.....and then between my people in Hong Kong/Taiwan with the local factories......and then a quote is generated and sent to my client......to samples being made and sent for approval.....to a PO being generated......to final samples being sent.....to the order being shipped and delivered to the clients warehouse. I was thinking of an animation showing arrows and text showing the back and forth communication and explaining how the process flows.

```html
<!DOCTYPE html>
<html lang="en">
<head>
<meta charset="utf-8">
<title>Brevard Trade Partners – Asian Outsourcing Made Easy</title>
<link rel="stylesheet" href="https://fonts.googleapis.com/css2?family=Open+Sans:wght@400;600;700&family=Roboto+Condensed:wght@400;700&family=Orbitron:wght@600&display=swap">
<style>
:root{
  --navy:#141a5e;
  --navy-deep:#0f1450;
  --green:#5e8f0f;
  --green-dark:#4d7a0b;
  --text:#333;
  --muted:#555;
  --panel:#f0f0f3;
  --line:#d9d9de;
  --white:#fff;
}
*{box-sizing:border-box;margin:0;padding:0}
html,body{width:1200px;height:2889px;overflow:hidden;background:var(--white)}
body{position:relative;font-family:"Open Sans",sans-serif;color:var(--text)}
ul{list-style:none}
.abs{position:absolute}

/* header */
.site-header{left:0;top:0;width:1200px;height:92px;background:var(--white)}
.brand{left:73px;top:26px;display:flex;align-items:center;gap:10px}
.brand-mark{width:14px;height:14px;background:var(--green);border-radius:50%}
.brand-name{font-family:"Roboto Condensed",sans-serif;font-weight:700;font-size:27px;color:var(--navy);letter-spacing:.5px}
.main-nav{left:584px;top:0;height:92px;display:flex}
.main-nav a{display:flex;align-items:center;height:92px;padding:0 19px;font-family:"Roboto Condensed",sans-serif;font-size:15px;color:#222;text-decoration:none;text-transform:uppercase}
.main-nav a.active{background:var(--green);color:var(--white);width:79px;justify-content:center;padding:0}
.main-nav a:nth-child(2){margin-left:22px}

/* hero */
.hero{left:0;top:92px;width:1200px;height:582px;background:linear-gradient(100deg,#c9b59e 0%,#b9a59a 30%,#d8d2d4 55%,#c7a9b6 75%,#6f8fb0 100%)}
.hero-title{font-family:"Orbitron",sans-serif;font-weight:600;color:var(--white);background:rgba(18,24,70,.82);letter-spacing:2px;display:flex;align-items:center;justify-content:center}
.hero-t1{left:630px;top:272px;width:497px;height:42px;font-size:33px}
.hero-t2{left:809px;top:324px;width:318px;height:46px;font-size:35px}
.hero-sub{left:626px;top:393px;width:501px;height:40px;background:rgba(50,50,50,.85);color:var(--white);font-family:"Roboto Condensed",sans-serif;font-size:20px;display:flex;align-items:center;justify-content:center}
.hero-arrow{top:466px;width:38px;height:38px;border-radius:50%;background:#111;display:flex;align-items:center;justify-content:center}

/* sidebar */
.side-box{left:73px;width:245px;border:1px solid var(--navy);background:var(--white)}
.side-box h3{background:var(--navy);color:var(--white);font-family:"Roboto Condensed",sans-serif;font-weight:700;font-size:14px;height:44px;line-height:44px;padding-left:18px;text-transform:uppercase}
.side-box ul{padding:4px 16px 10px 18px}
.side-box li{font-size:12.5px;color:#222;height:33px;line-height:33px;border-bottom:1px solid #e3e3e6;padding-left:18px;position:relative}
.side-box li:last-child{border-bottom:0}
.side-box li::before{content:"";position:absolute;left:4px;top:15px;width:5px;height:5px;border-radius:50%;background:#222}

/* intro */
.intro{left:345px;top:735px;width:782px}
.intro h1{font-size:27px;font-weight:600;color:var(--green);margin-bottom:14px}
.intro p{font-size:12.5px;line-height:22px;color:var(--muted)}

/* product cards */
.card{width:241px;height:301px;border:1px solid var(--line);background:var(--white);text-align:center}
.card-photo{margin:14px auto 0;width:213px;height:143px}
.card h2{font-family:"Roboto Condensed",sans-serif;font-weight:700;font-size:17px;color:var(--navy);margin-top:24px;text-transform:uppercase}
.card p{font-size:12.5px;line-height:18px;color:#333;padding:0 24px;margin-top:4px}
.btn-detail{display:inline-block;margin-top:14px;width:87px;height:29px;line-height:29px;background:var(--green);color:var(--white);font-family:"Roboto Condensed",sans-serif;font-size:13px;text-transform:uppercase}

/* about panel */
.about{left:73px;top:1545px;width:1054px;height:217px;background:var(--panel);text-align:center;padding:40px 22px 0}
.section-title{font-family:"Roboto Condensed",sans-serif;font-weight:700;font-size:27px;color:var(--navy);text-transform:uppercase}
.section-rule{width:74px;height:3px;background:var(--green);margin:6px auto 0}
.about p{font-size:12.5px;line-height:24px;color:var(--muted);margin-top:10px}

/* contact band */
.contact-band{left:73px;top:1791px;width:1054px;height:137px;background:linear-gradient(90deg,var(--green-dark),var(--green) 50%,var(--green-dark))}
.avatar{left:25px;top:22px;width:93px;height:93px;border-radius:50%;border:4px solid #e6e6e6;background:linear-gradient(160deg,#7b6a5c,#3c3a3a)}
.band-title{left:145px;top:28px;font-family:"Roboto Condensed",sans-serif;font-size:23px;color:var(--white)}
.band-sub{left:145px;top:60px;font-size:12.5px;color:var(--white)}
.band-contacts{left:145px;top:94px;display:flex;gap:30px;font-size:12.5px;color:var(--white)}
.band-contacts span{display:flex;align-items:center;gap:8px}
.btn-quote{left:824px;top:46px;width:195px;height:49px;background:var(--navy);color:var(--white);display:flex;align-items:center;justify-content:center;gap:9px;font-family:"Roboto Condensed",sans-serif;font-size:16px;text-transform:uppercase}

/* how it works */
.how-head{left:0;top:1983px;width:1200px;text-align:center}
.how-text{left:75px;top:2076px;width:640px}
.how-text h2{font-size:17px;font-weight:600;color:var(--green);margin-bottom:10px}
.how-text p{font-size:12.5px;line-height:21px;color:var(--muted)}
.btn-view{display:inline-block;margin-top:20px;width:125px;height:36px;line-height:36px;text-align:center;background:var(--green);color:var(--white);font-family:"Roboto Condensed",sans-serif;font-size:15px;text-transform:uppercase}
.video{left:751px;top:2063px;width:368px;height:227px;border:3px solid #e2e2e2;background:linear-gradient(120deg,#5b5b63,#8a8a90 45%,#bdb8b7)}
.play{left:160px;top:90px}

/* footer */
.site-footer{left:0;top:2346px;width:1200px;height:543px;background:linear-gradient(180deg,var(--navy-deep),var(--navy))}
.foot-col{top:46px;width:250px;color:var(--white)}
.foot-col h4{font-family:"Roboto Condensed",sans-serif;font-weight:700;font-size:15.5px;line-height:21px;text-transform:uppercase;margin-bottom:9px}
.foot-col ul{margin-bottom:24px}
.foot-col li{font-size:12px;line-height:27.7px}
.foot-brand{display:flex;align-items:center;gap:8px;margin-bottom:24px}
.foot-brand .brand-mark{background:var(--white);width:12px;height:12px}
.foot-brand span{font-family:"Roboto Condensed",sans-serif;font-weight:700;font-size:17px}
.foot-address{font-size:12px;line-height:19px}
.foot-address p+p{margin-top:19px}
</style>
</head>
<body>

<header class="site-header abs">
  <div class="brand abs"><span class="brand-name">BREVARD TRADE PARTNERS</span><span class="brand-mark"></span></div>
  <nav class="main-nav abs">
    <a class="active" href="#">Home</a>
    <a href="#">Product Categories</a>
    <a href="#">About Us</a>
    <a href="#">Request Quote</a>
  </nav>
</header>

<section class="hero abs" role="img" aria-label="Photo of a smiling seamstress working at a sewing machine in a bright textile workshop">
</section>
<div class="hero-title hero-t1 abs">ASIAN OUTSOURCING</div>
<div class="hero-title hero-t2 abs">MADE EASY!</div>
<div class="hero-sub abs">Custom Sewn Goods Made to Your Specifications</div>
<div class="hero-arrow abs" style="left:1036px"><svg width="14" height="14" viewBox="0 0 14 14"><path d="M9 2 4 7l5 5" fill="none" stroke="#fff" stroke-width="2"/></svg></div>
<div class="hero-arrow abs" style="left:1081px"><svg width="14" height="14" viewBox="0 0 14 14"><path d="m5 2 5 5-5 5" fill="none" stroke="#fff" stroke-width="2"/></svg></div>

<aside class="side-box abs" style="top:742px">
  <h3>Sourcing Solutions</h3>
  <ul><li>Bags</li><li>Cases</li><li>Covers</li><li>Gloves</li><li>Medical</li><li>Sewn Goods</li><li>Sporting Goods</li></ul>
</aside>
<aside class="side-box abs" style="top:1059px">
  <h3>What You Need to Know</h3>
  <ul><li>Contract Sewing in China</li><li>What is the Process?</li><li>What the Minimum Order?</li><li>Contract Outsourcing FAQ</li><li>Outsourcing Case Study</li><li>Custom Industrial Sewing in China</li></ul>
</aside>

<section class="intro abs">
  <h1>Sourcing custom goods in China</h1>
  <p>We outsource sewing services direct from China. Our long-established and extensive network of offshore factory-partners provides our clients with access to a wide variety of contract sewing expertise from Chinese manufacturers. Clients only need to communicate with our US agents, but will have the benefits of the cost savings &amp; quality workmanship from offshore outsourcing from Asia.</p>
</section>

<article class="card abs" style="left:345px;top:878px">
  <div class="card-photo" role="img" aria-label="Close-up of red fabric being stitched under a sewing machine" style="background:linear-gradient(135deg,#6b4a3e,#c23a2c 60%,#e8c3b0)"></div>
  <h2>Sewn Goods</h2><p>Neque porro quisquam est qui est dolorem ipsum quia dolor.</p><span class="btn-detail">Detail</span>
</article>
<article class="card abs" style="left:614px;top:878px">
  <div class="card-photo" role="img" aria-label="Black messenger bag with red and grey stripes" style="background:radial-gradient(ellipse at center,#3a3a3a 0%,#6a6a6a 40%,#fff 72%)"></div>
  <h2>Bags</h2><p>Neque porro quisquam est qui est dolorem ipsum quia dolor.</p><span class="btn-detail">Detail</span>
</article>
<article class="card abs" style="left:884px;top:878px">
  <div class="card-photo" role="img" aria-label="Pair of white and black work gloves" style="background:radial-gradient(ellipse at center,#9a9a9a 0%,#d8d8d8 40%,#fff 70%)"></div>
  <h2>Gloves</h2><p>Neque porro quisquam est qui est dolorem ipsum quia dolor.</p><span class="btn-detail">Detail</span>
</article>
<article class="card abs" style="left:345px;top:1204px">
  <div class="card-photo" role="img" aria-label="Motorcycle under a navy blue protective cover" style="background:radial-gradient(ellipse at center,#1d2a6b 0%,#3a4a8f 40%,#fff 72%)"></div>
  <h2>Covers</h2><p>Neque porro quisquam est qui est dolorem ipsum quia dolor.</p><span class="btn-detail">Detail</span>
</article>
<article class="card abs" style="left:614px;top:1204px">
  <div class="card-photo" role="img" aria-label="Row of colourful phone cases" style="background:linear-gradient(90deg,#fff 8%,#3b3b9a 15%,#8a2f9e 30%,#c22a5e 45%,#d8732a 60%,#c9a227 72%,#fff 85%)"></div>
  <h2>Casses</h2><p>Neque porro quisquam est qui est dolorem ipsum quia dolor.</p><span class="btn-detail">Detail</span>
</article>
<article class="card abs" style="left:884px;top:1204px">
  <div class="card-photo" role="img" aria-label="Red, black and white golf bags" style="background:radial-gradient(ellipse at center,#b3232a 0%,#2a2a2a 40%,#fff 72%)"></div>
  <h2>Sporting Goods</h2><p>Neque porro quisquam est qui est dolorem ipsum quia dolor.</p><span class="btn-detail">Detail</span>
</article>

<section class="about abs">
  <h2 class="section-title">Don't Go at It Alone!</h2>
  <div class="section-rule"></div>
  <p>Brevard Trade Partners has been sourcing custom sewn goods in Asia since 1998. We work with our clients by matching their unique production needs with the best possible China sewing factories. We manage the entire process from start to finish, by first identifying the best factories to quote each job. The next step is negotiating the best (fair) price possible. We complete the process by monitoring the quality of the goods during production, and then managing the ocean logistics, customs clearances and local delivery right to your door. Our services and our total commitment to customer satisfaction help level the playing field by giving our customers access to low cost, high quality China contract sewing.</p>
</section>

<section class="contact-band abs">
  <div class="avatar abs" role="img" aria-label="Portrait photo of the company's sourcing agent"></div>
  <div class="band-title abs">Outsource Your Sewing Needs to Trusted Contractors in China</div>
  <div class="band-sub abs">Please contact us for immediate consultation regarding your outsourcing project.</div>
  <div class="band-contacts abs">
    <span><svg width="12" height="12" viewBox="0 0 24 24"><path fill="#fff" d="M6.6 10.8a15 15 0 0 0 6.6 6.6l2.2-2.2c.3-.3.7-.4 1-.2 1.1.4 2.3.6 3.6.6.6 0 1 .4 1 1V20c0 .6-.4 1-1 1A17 17 0 0 1 3 4c0-.6.4-1 1-1h3.5c.6 0 1 .4 1 1 0 1.3.2 2.5.6 3.6.1.3 0 .7-.2 1z"/></svg>Tel: 555-214-7730</span>
    <span><svg width="13" height="12" viewBox="0 0 24 22"><path fill="#fff" d="M6 0h12v6H6zM2 8h20v10h-4v4H6v-4H2zm6 6v6h8v-6z"/></svg>Fax: 555-214-7731</span>
    <span><svg width="13" height="10" viewBox="0 0 24 18"><path fill="#fff" d="M0 0h24v2L12 10 0 2zm0 4 12 8 12-8v14H0z"/></svg>Email: info@brevardtradepartners.com</span>
  </div>
  <div class="btn-quote abs"><svg width="16" height="14" viewBox="0 0 24 20"><path fill="#fff" d="M2 0h14a2 2 0 0 1 2 2v8a2 2 0 0 1-2 2H7l-5 4v-4a2 2 0 0 1-2-2V2a2 2 0 0 1 2-2zm18 5h2a2 2 0 0 1 2 2v8a2 2 0 0 1-2 2v3l-4-3h-7a2 2 0 0 1-2-2v-1h7a4 4 0 0 0 4-4z"/></svg>Request Quote</div>
</section>

<div class="how-head abs">
  <h2 class="section-title">How It Works</h2>
  <div class="section-rule"></div>
</div>
<section class="how-text abs">
  <h2>Neque porro quisquam est qui dolorem</h2>
  <p>Lorem ipsum dolor sit amet, consectetur adipiscing elit, sed do eiusmod tempor incididunt ut labore et dolore magna aliqua. Ut enim ad minim veniam, quis nostrud exercitation ullamco laboris nisi ut aliquip ex ea commodo consequat. Duis aute irure dolor in reprehenderit in voluptate velit esse cillum dolore eu fugiat nulla pariatur. Excepteur sint occaecat cupidatat non proident, sunt in culpa qui officia deserunt mollit anim id est laborum.</p>
  <span class="btn-view">View All</span>
</section>
<div class="video abs" role="img" aria-label="Video still of a woman in a sewing studio explaining the sourcing process">
  <svg class="play abs" width="60" height="60" viewBox="0 0 60 60"><circle cx="30" cy="30" r="26" fill="none" stroke="#fff" stroke-width="5"/><path d="M24 18v24l19-12z" fill="#fff"/></svg>
</div>

<footer class="site-footer abs">
  <div class="foot-col abs" style="left:75px">
    <h4>Custom Bags</h4>
    <ul><li>Athletic Bags</li><li>Backpacks</li><li>Computer Bags</li><li>Cooler Bags</li><li>Cosmetic Bags</li><li>Handbags</li><li>Messenger Bags</li><li>Shopping Bags</li><li>Tool Bags</li><li>Travel Bags</li><li>Yoga Bags</li></ul>
    <h4>Custom Cases</h4>
    <ul><li>Cosmetic Cases</li><li>Phone Cases</li><li>Tool Bags and Tool Cases</li></ul>
  </div>
  <div class="foot-col abs" style="left:345px">
    <h4>Custom Covers</h4>
    <ul><li>ATV Covers</li><li>Chair Covers</li><li>Equipment Covers</li><li>Golf Cart Covers</li><li>Motorcycle Covers</li><li>Outdoor Furniture Covers</li><li>Outdoor Grill Cover</li><li>Personal Watercraft Covers</li><li>Snowmobile Covers</li></ul>
    <h4>Custom Gloves</h4>
    <ul><li>Batting Gloves</li><li>Garden Gloves</li><li>Mechanic Gloves</li><li>Safety Gloves</li><li>Ski Gloves</li></ul>
  </div>
  <div class="foot-col abs" style="left:614px">
    <h4>Custom Medical<br>Accessories</h4>
    <ul><li>Medical Equipment Covers</li><li>Medical Pads</li><li>Medical Sheets &amp; Bedding Supplies</li><li>Oxygen Tank Cases and Bags</li></ul>
    <h4>Custom Sewn<br>Goods</h4>
    <ul><li>Pet Collars, Leashes, &amp; Harnesses</li><li>Socks</li></ul>
    <h4>Custom Sporting<br>Goods</h4>
    <ul><li>Yoga Mats</li><li>Yoga Gear and Accessories</li></ul>
  </div>
  <div class="foot-col abs" style="left:926px">
    <div class="foot-brand"><span class="brand-mark"></span><span>BREVARD TRADE PARTNERS</span></div>
    <h4>US Headquarters</h4>
    <div class="foot-address">
      <p>Brevard Trade Partners, LLC<br>48 Harbor Street<br>Suite B-2<br>Lakeport, NH 03299</p>
      <p>Online: Inquiry Form<br>Tel: 555-214-7730<br>Fax: 555-214-7731<br>Email: info@brevardtradepartners.com</p>
      <p style="margin-top:38px">© Brevard Trade Partners, LLC. |<br>USA - Hong Kong - Taipei</p>
    </div>
  </div>
</footer>

</body>
</html>
```